Help Give House Painter “Fresh” Website Makeover!

A residential and commercial painting company based in Albuquerque, NM, USA needs a fresh, new, fun, and playful--yet, simple, elegant and professional--website made.

Here is a link to their existing site:

http://corvelcoatings.example/

We want to keep a similar site structure., So the navigation layout will stay the same. However, the video is too small, is too far over in the sidebar, and the overall design is amateur at best. We want something bright, colorful and bold!

We will need a space for the Video above the fold, and there needs to be space in the design for Testimonials, Specials and Images. It’s also very important to have the Pellham Roster awards that you see on his current website.

Please also include somewhere in the Design icons for YouTube, Facebook, Google+ and LinkedIn.

Here are some examples to look at to get your creative juices flowing!

http://brightloombrush.example/

http://www.tkvr.example/

http://www.marblow-tennick.example/

http://www.quarrypages.example/painting-company-niche-website/

http://www.brisklayoutdepot.example/website-templates/painting-company-website-template-53817.html

We have accounts at both lumavault.example and pixaroo.example. If you use placeholder images from there, that's fine. We can buy the images when and if your design is selected.

Target Market(s)

The audience is the average middle class homeowner to higher upper class. This should appeal to families, couples, and singles who own a home.

Industry/Entity Type

Residential

Font styles to use
Sans Serif

Requirements
Must have
• - - Lots of color! It's a site about painting homes. People like a variety of colors. Bring out your inner artist, and get bold with your colors!

- - A video place holder. As you can see, there is a video on the existing site, but it's small and hidden. Make it big and put it top left, or in the center.

- -Detailed and organized PSD structure. We're going to turn your design into a website, and to make that work soothly, we ask that you organize you PSD well: name your layers, keep things separated, group and ungroup as necessary, etc.

- A sidebar that goes down the right side of an interior page. We need a homepage, and also one [1] interior page template. We don't need you to make a design for each page. Just the homepage, followed by a simple interior page design that requires only the header/navigation, and a sidebar down the right side.
Should not have
• - Coding. This is a design project only.

```html
<!DOCTYPE html>
<html lang="en">
<head>
<meta charset="utf-8">
<title>Corvel Coatings — Residential &amp; Commercial Painting</title>
<link href="https://fonts.googleapis.com/css2?family=Lato:ital,wght@0,400;0,700;0,900;1,400&family=Open+Sans:ital,wght@0,400;0,600;0,700;1,400&display=swap" rel="stylesheet">
<style>
:root{
  --brand-blue:#1e63b6;
  --nav-top:#2a86d6;
  --nav-bottom:#0c5aa8;
  --accent-red:#e2202a;
  --ink:#333;
  --muted:#666;
  --navy:#1b2a47;
  --navy-deep:#131e35;
  --sky:#d9ebf8;
  --orange:#f47a10;
  --cyan:#39a9e8;
  --green:#55a715;
  --gold:#d9a521;
  --white:#fff;
}
*{box-sizing:border-box;margin:0;padding:0}
html,body{width:752px;height:1200px;overflow:hidden}
body{position:relative;font-family:"Open Sans",Arial,sans-serif;color:var(--ink);background:var(--white)}
.abs{position:absolute}

/* header */
.site-header{left:0;top:0;width:752px;height:88px;background:linear-gradient(#fafafa,#ececec)}
.logo{left:82px;top:24px;display:flex;align-items:center;gap:8px}
.logo-dot{width:40px;height:40px;border-radius:50%;background:var(--brand-blue)}
.logo-name{font-family:Lato,sans-serif;font-weight:900;font-size:21px;color:var(--brand-blue);letter-spacing:.3px}
.tagline{left:160px;top:52px;font-family:Lato,sans-serif;font-size:9px;letter-spacing:1.3px;color:#555;border-top:1px solid #bbb;padding-top:1px}
.badge{width:34px;height:46px;top:14px;background:linear-gradient(#f0c64a,var(--gold));border-radius:4px 4px 17px 17px;border:2px solid #3a3a3a}
.badge-label{top:66px;font-size:7px;font-weight:600;color:var(--brand-blue);width:80px;text-align:center}
.phone{left:560px;top:19px;display:flex;align-items:center;gap:6px;font-family:Lato,sans-serif;font-size:16px;color:var(--accent-red)}
.cta{left:538px;top:49px;width:133px;height:21px;background:linear-gradient(#2a86d6,#0d5cae);border-radius:3px;color:#fff;font-family:Lato,sans-serif;font-weight:700;font-size:11px;text-align:center;line-height:21px}

/* nav */
.main-nav{left:0;top:88px;width:752px;height:29px;background:linear-gradient(var(--nav-top),var(--nav-bottom))}
.main-nav ul{list-style:none;display:flex;gap:15px;position:absolute;left:82px;top:9px}
.main-nav li{font-family:Lato,sans-serif;font-weight:700;font-size:9.5px;color:#fff;position:relative}
.main-nav li.current::after{content:"";position:absolute;left:0;right:0;bottom:-7px;height:2px;background:#fff}

/* hero */
.hero{left:0;top:117px;width:752px;height:238px;background:linear-gradient(90deg,#9c8f84 0%,#c9c4bd 35%,#e5e5e2 60%,#d8d6d2 100%)}
.hero-title{left:84px;top:260px;font-family:Arial,sans-serif;font-weight:700;font-size:20px;line-height:22px;color:var(--accent-red);text-shadow:0 0 3px #fff,0 0 3px #fff}
.video{left:422px;top:145px;width:246px;height:165px;background:#fff;padding:6px;box-shadow:0 2px 6px rgba(0,0,0,.35)}
.video-still{width:234px;height:130px;background:linear-gradient(135deg,#c8d3c2,#e8e9e4 60%,#9aa4b4)}
.video-bar{width:234px;height:23px;background:linear-gradient(#3b3f45,#1d1f22);position:relative}
.play-btn{left:530px;top:210px;width:32px;height:22px;background:var(--accent-red);border-radius:6px}
.dots{left:617px;top:328px;display:flex;gap:4px}
.dots span{width:10px;height:10px;border-radius:50%;background:#fff;border:1px solid #999}
.dots span.on{background:var(--accent-red)}

/* intro */
.intro{left:0;top:355px;width:752px;height:235px;background:linear-gradient(#e9f3fb,var(--sky))}
.card{background:#fff;border:1px solid #cfe0ee;box-shadow:0 2px 4px rgba(0,0,0,.12)}
.card h2{font-family:Lato,sans-serif;font-weight:700;font-size:15px;color:var(--brand-blue)}
.card h2 em{font-style:normal;color:var(--accent-red)}
.welcome{left:84px;top:387px;width:291px;height:166px;padding:8px 11px}
.welcome p{font-size:8.4px;line-height:13px;color:#555;margin-top:6px;letter-spacing:.2px}
.social{display:flex;gap:6px;margin-top:8px}
.social span{width:18px;height:18px;border-radius:2px}
.estimate{left:389px;top:387px;width:280px;height:166px;padding:8px 11px}
.estimate p{font-size:7.4px;line-height:10px;color:#555;margin-top:4px}
.field{position:absolute;height:15px;border:1px solid #bbb;border-radius:2px;font-size:7px;color:#444;padding:2px 4px;background:#fff}
.submit{position:absolute;left:11px;top:139px;width:121px;height:19px;background:var(--accent-red);color:#fff;font-weight:700;font-size:10px;text-align:center;line-height:19px;border-radius:2px}

/* features */
.features{left:0;top:590px;width:752px;height:343px;background:radial-gradient(ellipse at 50% 40%,#2b3d60,var(--navy-deep))}
.feature{top:627px;width:172px;height:255px;text-align:center;color:#fff}
.feature h3{font-family:Lato,sans-serif;font-weight:700;font-size:13.5px;line-height:17px;margin-top:9px}
.feature .pic{margin:9px auto 0;width:153px;height:96px;background:#fff;padding:6px}
.feature .pic div{width:100%;height:100%}
.feature p{font-size:8.3px;line-height:13px;color:#111;margin:12px 10px 0}
.feature .more{font-family:Lato,sans-serif;font-weight:700;font-size:8.5px;color:#111;margin-top:9px}
.orange{left:84px;background:var(--orange)}
.blue{left:291px;background:var(--cyan)}
.green{left:493px;background:var(--green)}

/* reviews */
.reviews{left:0;top:933px;width:752px;height:207px;background:linear-gradient(#e4f0fa,#cfe3f4)}
.reviews h2{position:absolute;left:0;width:752px;top:22px;text-align:center;font-family:Lato,sans-serif;font-weight:700;font-size:18px;color:var(--brand-blue)}
.reviews h2 em{font-style:normal;color:var(--accent-red)}
.reviews .sub{position:absolute;left:0;width:752px;top:46px;text-align:center;font-size:9px;color:#666}
.stars{position:absolute;left:358px;top:61px;color:var(--gold);font-size:11px;letter-spacing:1px}
.rule{position:absolute;left:280px;top:68px;width:190px;height:1px;background:#b8cde0}
.quote{position:absolute;left:82px;top:85px;width:492px;height:62px;background:#fff;border-radius:4px;padding:10px 14px 0 32px;font-size:7.9px;line-height:12.5px;font-style:italic;color:#444}
.quote::before{content:"\201C";position:absolute;left:12px;top:-2px;font-size:28px;color:#bbb;font-style:normal;font-family:Georgia,serif}
.avatar{position:absolute;left:585px;top:83px;width:72px;height:72px;border-radius:50%;background:linear-gradient(#dfe7ee,#9fb1c4);border:3px solid #fff;box-shadow:0 1px 4px rgba(0,0,0,.25)}
.author{position:absolute;left:490px;top:160px;font-size:7.5px;font-style:italic;font-weight:600;color:#333}

/* footer */
.site-footer{left:0;top:1140px;width:752px;height:60px;background:var(--navy);text-align:center;color:#fff}
.site-footer .links{margin-top:20px;font-family:Lato,sans-serif;font-weight:700;font-size:7.6px;letter-spacing:.2px}
.site-footer .copy{margin-top:5px;font-size:7px;color:#dde}
</style>
</head>
<body>

<header class="abs site-header">
  <div class="abs logo"><span class="logo-dot"></span><span class="logo-name">CORVEL COATINGS</span></div>
  <div class="abs tagline">NOT JUST ANOTHER PAINTER</div>
  <div class="abs badge" style="left:409px" role="img" aria-label="Pellham Roster service award"></div>
  <div class="abs badge" style="left:473px" role="img" aria-label="Pellham Roster service award"></div>
  <div class="abs badge-label" style="left:384px">Exterior Painting</div>
  <div class="abs badge-label" style="left:449px">Interior Painting</div>
  <div class="abs phone">
    <svg width="15" height="15" viewBox="0 0 16 16"><circle cx="8" cy="8" r="7" fill="none" stroke="#1e63b6" stroke-width="1.5"/><path d="M5.5 4.5l1.5 1.5-1 1c.6 1.2 1.6 2.2 2.8 2.8l1-1 1.5 1.5-1.2 1.2C7.8 11 5 8.2 4.3 5.7z" fill="#1e63b6"/></svg>
    123 456 7890
  </div>
  <div class="abs cta">FREE ESTIMATES</div>
</header>

<nav class="abs main-nav">
  <ul>
    <li class="current">HOME</li><li>ABOUT US</li><li>RESIDENTIAL PAINTING</li><li>COMMERCIAL PAINTING</li><li>FAQ</li><li>SPECIALS</li><li>BLOG</li><li>TESTIMONIALS</li><li>CONTACT US</li>
  </ul>
</nav>

<section class="abs hero" role="img" aria-label="Laughing child with colourful paint on her face"></section>
<h1 class="abs hero-title">Residential &amp; Commercial<br>Painting Company</h1>
<div class="abs video">
  <div class="video-still" role="img" aria-label="Video still of a painter rolling paint onto a wall"></div>
  <div class="video-bar">
    <svg width="234" height="23" viewBox="0 0 234 23">
      <path d="M10 7l6 4.5-6 4.5z" fill="#fff"/>
      <path d="M28 9h3l3-3v11l-3-3h-3z" fill="#fff"/>
      <rect x="44" y="10" width="128" height="3" rx="1.5" fill="#555"/>
      <rect x="44" y="10" width="62" height="3" rx="1.5" fill="#3b8fe0"/>
      <path d="M218 7h5v5M223 7l-5 5M212 16h-5v-5M207 16l5-5" stroke="#fff" stroke-width="1.4" fill="none"/>
    </svg>
  </div>
</div>
<svg class="abs play-btn" viewBox="0 0 32 22"><path d="M13 6l8 5-8 5z" fill="#fff"/></svg>
<div class="abs dots"><span></span><span class="on"></span><span></span><span></span></div>

<section class="abs intro"></section>
<article class="abs card welcome">
  <h2>Welcome To CORVEL <em>COATINGS</em></h2>
  <p>Corvel Coatings does jobs as small as a bathroom up to large commercial projects right here in Albuquerque and Rio Rancho. Extensive as an entire apartment exterior, to a kitchen and all home interior, no job is too big or too small for Corvel Coatings of Albuquerque. Corvel Coatings is staffed with the best painters for the highest quality paint jobs. Corvel Coatings is not a community's average house painter staffing company, but this painting company is staffed with professional painters...</p>
  <div class="social">
    <span style="background:#3b5a9a" role="img" aria-label="Social profile link"></span>
    <span style="background:#4fb6e3" role="img" aria-label="Social profile link"></span>
  </div>
</article>
<form class="abs card estimate">
  <h2>Schedule <em>Free Estimate</em></h2>
  <p>How to Schedule an Estimae Requesting an estimate online is very simple and easy. Fill out the Form below and we will send you a rough quote to your email. We may also call you if we have any more questions.</p>
  <div class="field" style="left:11px;top:70px;width:123px">First Name</div>
  <div class="field" style="left:147px;top:70px;width:123px">Email</div>
  <div class="field" style="left:11px;top:91px;width:123px">Phone</div>
  <div class="field" style="left:147px;top:91px;width:123px;height:35px">Decribe what needs to be done.</div>
  <div class="field" style="left:11px;top:111px;width:56px;font-style:italic;letter-spacing:2px">A8OC</div>
  <div class="field" style="left:73px;top:111px;width:61px"></div>
  <div class="submit">SUBMIT</div>
</form>

<section class="abs features"></section>
<article class="abs feature orange">
  <h3>Our Painting<br>In Albuquerque</h3>
  <div class="pic"><div role="img" aria-label="Couple painting a wall green" style="background:linear-gradient(120deg,#e8d4c8,#b7d98a)"></div></div>
  <p>Corvel Coatings does jobs as small as a bathroom up to large commercial projects right here in Albuquerque.</p>
  <div class="more">Read More &rsaquo;&rsaquo;</div>
</article>
<article class="abs feature blue">
  <h3>Albuquerque<br>Painter Videos</h3>
  <div class="pic"><div role="img" aria-label="Paint roller spreading orange paint" style="background:linear-gradient(120deg,#e7a63a,#d58a1c)"></div></div>
  <p>TWe have shot a ton of videos with our team answering all of your most frequently asked questions. We want</p>
  <div class="more">Read More &rsaquo;&rsaquo;</div>
</article>
<article class="abs feature green">
  <h3>Happy Albuquerque<br>Painting Customers</h3>
  <div class="pic"><div role="img" aria-label="Woman painting a wall light blue" style="background:linear-gradient(120deg,#f2f4f6,#a9cbe6)"></div></div>
  <p>100% Customer Satisfaction is our Ultimate Goal. We are proud to have served so many clients in an around</p>
  <div class="more">Read More &rsaquo;&rsaquo;</div>
</article>

<section class="abs reviews">
  <h2>Our Customer <em>Review</em></h2>
  <div class="sub">Lorem ipsum dolor sit amet, consectetur Donec a consequat mag&nbsp; Aenean eu velit&nbsp; Aenean sollicitudin</div>
  <div class="rule"></div>
  <div class="stars">&#9733;&#9733;&#9733;</div>
  <blockquote class="quote">Lorem sum dolor sit amet, consectetuer adipiscing elit, sed diam nonummy nibh euismod tincidunt ut laoreet re agn aliqam erat volutpat wisi enim ad minim veniam, quis nostrud exerci tation ullamcorper suscipit lobortis nisl ut aliquip modo conseuatis autem vel eum iriure dolor in hendrerit in vulputate velit esse molestie consequat, vel illum dolore eu.</blockquote>
  <div class="avatar" role="img" aria-label="Customer portrait"></div>
  <div class="author">Darel, Northvane , USA</div>
</section>

<footer class="abs site-footer">
  <div class="links">HOME &nbsp;|&nbsp; ABOUT US &nbsp;|&nbsp; RESIDENTIAL PAINTING &nbsp;|&nbsp; COMMERCIAL PAINTING &nbsp;|&nbsp; FAQ &nbsp;|&nbsp; SPECIALS &nbsp;|&nbsp; BLOG &nbsp;|&nbsp; TESTIMONIALS &nbsp;|&nbsp; CONTACT US</div>
  <div class="copy">&copy; 2015 CORVEL COATINGS. ALL RIGHT RESERVED.</div>
</footer>

</body>
</html>
```